Calendar Design Project: 2025 with Specific Edits

This is a straightforward project where your creativity can shine!
Simply take the existing 2024 calendar and adapt it for 2025 by incorporating the new photos I've attached.
Please keep the overall concept of the 2024 calendar intact—your focus will be on enhancing it with fresh visuals.

I can't wait to see your amazing designs!
I am looking for a talented graphic designer to create a new 2025 calendar with specific adjustments.
Pictures attached.
Requirements:
Calendar Size: 52cm x 34cm
March Folder:
Adjust the image named "attached - DJI-0025" to make the circular road darker to match the rest of the design.
May Folder:
Modify the circled area in the May image to ensure it looks consistent with the other road (reference file: "attached - After").
November Folder:
Clear out the circled area in the November image (reference file: "attached - After1").
Please let me know if you have any questions or need further clarification.
I added to my breif a design i made last year for same client.
2025, calendar should be vertical and not horizontal. and some of the photos attache are "Before" and "After" please include together inside each month of the calendar.
Thank you!
Feel free to adjust any details as necessary!

Hello talented designers!

I’m excited to share that this is my 14th project on the ArtHive platform, and I’ve been fortunate to have successful collaborations in the past. I'm looking forward to creating a new 2025 calendar with your help, and I believe that with your creativity and skills, we can make this project a success as well!

I hope to establish a long-term relationship with a talented team like yours. As an added incentive, I will be offering a bonus for the winner, and I may select more than one winner, so everyone has a chance to shine!

Let’s make something amazing together!

Best
Update:
cancel or before, only place the After picture

Requirements
Must have
• Project Overview Objective: Create a 2025 calendar using the provided images, maintaining the design concept from the 2024 calendar but enhancing it with new visuals. Format: Vertical layout (52cm x 34cm).

```html
<!DOCTYPE html>
<html lang="en">
<head>
<meta charset="utf-8">
<title>Kerro Construction 2025 Wall Calendar</title>
<link rel="stylesheet" href="https://fonts.googleapis.com/css2?family=Open+Sans:wght@400;600;700&display=swap">
<style>
:root{
  --green:#6fe12a;
  --green-bright:#8ef43a;
  --green-pale:#e6fbd6;
  --weekend:#ccf7b4;
  --cell:#eff2f2;
  --ink:#1c1c1c;
  --grey:#5e6366;
  --shadow:rgba(20,20,20,.75);
}
*{margin:0;padding:0;box-sizing:border-box}
html,body{width:1200px;height:848px;overflow:hidden;background:#fff}
body{position:relative;font-family:"Open Sans",Arial,sans-serif;color:var(--ink)}
.page{position:absolute;top:130px;width:385px;height:588px;background:#fff;overflow:hidden;box-shadow:9px 9px 7px var(--shadow)}
.page--sep{left:9px}.page--oct{left:411px}.page--nov{left:808px}
.header-art{position:absolute;left:0;top:0;width:385px;height:312px}
.brand{position:absolute;left:34px;top:24px;display:flex;align-items:flex-start;gap:4px}
.brand__mark{width:10px;height:10px;background:var(--green);margin-top:6px}
.brand__name{font-weight:700;font-size:24px;line-height:24px;letter-spacing:1px;color:#2b2b2b}
.brand__sub{font-size:8.5px;letter-spacing:.4px;color:#2b2b2b;margin-top:1px}
.title-label{position:absolute;left:18px;top:313px;font-size:16px;line-height:18px;color:var(--green)}
.title-year{position:absolute;left:17px;top:327px;font-size:35px;line-height:40px;font-weight:600;letter-spacing:.5px}
.title-month{position:absolute;left:156px;top:342px;font-size:22px;line-height:26px;color:var(--grey);letter-spacing:.8px}
.month-grid{position:absolute;left:18px;top:378px;width:256px;display:grid;grid-template-columns:repeat(7,1fr);grid-template-rows:20px repeat(5,25px);column-gap:1.5px;row-gap:6.3px}
.month-grid span{background:var(--cell);font-size:13.5px;line-height:13px;padding:0 0 2px 5px;display:flex;align-items:flex-end}
.month-grid .wd{font-size:5px;font-weight:600;justify-content:center;align-items:center;padding:0}
.month-grid span:nth-child(7n+1),.month-grid span:nth-child(7n){background:var(--weekend)}
.mini{position:absolute;left:281px;width:87px}
.mini--a{top:377px}.mini--b{top:485px}
.mini__title{font-size:5.6px;line-height:7px;color:var(--grey);letter-spacing:.2px}
.mini__title b{font-weight:400;color:var(--green)}
.mini__grid{margin-top:2px;display:grid;grid-template-columns:repeat(7,1fr);grid-template-rows:4px repeat(5,8px);column-gap:1px;row-gap:2.4px}
.mini__grid span{font-size:4.2px;line-height:8px;padding-left:1px;background:#fff}
.mini__grid .wd{font-size:1.8px;line-height:4px;text-align:center;background:var(--cell);padding:0}
.mini__grid span:nth-child(7n+1),.mini__grid span:nth-child(7n){background:var(--weekend)}
.footer{position:absolute;left:20px;top:563px;width:355px;display:flex;align-items:flex-end;gap:10px;font-size:4.4px;color:var(--grey)}
.footer__brand{font-weight:700;font-size:10px;line-height:10px;color:#2b2b2b}
.footer__brand small{display:block;font-weight:400;font-size:2.7px;line-height:3px}
.footer__item{white-space:nowrap;line-height:6px}
.footer__item b{font-weight:400;color:var(--green)}
</style>
</head>
<body>

<!-- SEPTEMBER -->
<section class="page page--sep">
  <svg class="header-art" viewBox="0 0 385 312">
    <defs>
      <linearGradient id="band" x1="0" y1="0" x2="1" y2="0"><stop offset="0" stop-color="#f2fde8"/><stop offset=".6" stop-color="#b5f57c"/><stop offset="1" stop-color="#8ef43a"/></linearGradient>
      <linearGradient id="photoSep" x1="0" y1="0" x2="0" y2="1"><stop offset="0" stop-color="#7e9f6a"/><stop offset=".45" stop-color="#8e8a70"/><stop offset="1" stop-color="#c95a56"/></linearGradient>
    </defs>
    <path d="M0 0H385V48C300 36 220 60 150 85C90 104 40 98 0 86Z" fill="url(#band)"/>
    <path d="M0 240C60 265 120 275 200 272C290 268 340 250 385 240V310C300 305 200 290 100 275C60 270 25 268 0 270Z" fill="url(#band)"/>
    <path role="img" aria-label="Photo: road grading works with dump trucks and site crew" d="M0 84C60 96 110 82 190 56C260 34 330 35 385 40V222C330 242 250 260 180 256C100 252 40 252 0 260Z" fill="url(#photoSep)"/>
  </svg>
  <div class="brand"><span class="brand__mark"></span><div><div class="brand__name">KERRO</div><div class="brand__sub">CONSTRUCTION LTD</div></div></div>
  <div class="title-label">CALENDAR</div>
  <div class="title-year">2025</div>
  <div class="title-month">SEPTEMBER</div>
  <div class="month-grid">
    <span class="wd">SUNDAY</span><span class="wd">MONDAY</span><span class="wd">TUESDAY</span><span class="wd">WEDNESDAY</span><span class="wd">THURSDAY</span><span class="wd">FRIDAY</span><span class="wd">SATURDAY</span>
    <span></span><span>1</span><span>2</span><span>3</span><span>4</span><span>5</span><span>6</span>
    <span>7</span><span>8</span><span>9</span><span>10</span><span>11</span><span>12</span><span>13</span>
    <span>14</span><span>15</span><span>16</span><span>17</span><span>18</span><span>19</span><span>20</span>
    <span>21</span><span>22</span><span>23</span><span>24</span><span>25</span><span>26</span><span>27</span>
    <span>28</span><span>29</span><span>30</span><span></span><span></span><span></span><span></span>
  </div>
  <div class="mini mini--a"><div class="mini__title">AUGUST | <b>2025</b></div>
    <div class="mini__grid">
      <span class="wd">SUNDAY</span><span class="wd">MONDAY</span><span class="wd">TUESDAY</span><span class="wd">WEDNESDAY</span><span class="wd">THURSDAY</span><span class="wd">FRIDAY</span><span class="wd">SATURDAY</span>
      <span>31</span><span></span><span></span><span></span><span></span><span>1</span><span>2</span>
      <span>3</span><span>4</span><span>5</span><span>6</span><span>7</span><span>8</span><span>9</span>
      <span>10</span><span>11</span><span>12</span><span>13</span><span>14</span><span>15</span><span>16</span>
      <span>17</span><span>18</span><span>19</span><span>20</span><span>21</span><span>22</span><span>23</span>
      <span>24</span><span>25</span><span>26</span><span>27</span><span>28</span><span>29</span><span>30</span>
    </div></div>
  <div class="mini mini--b"><div class="mini__title">OCTOBER | <b>2025</b></div>
    <div class="mini__grid">
      <span class="wd">SUNDAY</span><span class="wd">MONDAY</span><span class="wd">TUESDAY</span><span class="wd">WEDNESDAY</span><span class="wd">THURSDAY</span><span class="wd">FRIDAY</span><span class="wd">SATURDAY</span>
      <span></span><span></span><span></span><span>1</span><span>2</span><span>3</span><span>4</span>
      <span>5</span><span>6</span><span>7</span><span>8</span><span>9</span><span>10</span><span>11</span>
      <span>12</span><span>13</span><span>14</span><span>15</span><span>16</span><span>17</span><span>18</span>
      <span>19</span><span>20</span><span>21</span><span>22</span><span>23</span><span>24</span><span>25</span>
      <span>26</span><span>27</span><span>28</span><span>29</span><span>30</span><span>31</span><span></span>
    </div></div>
  <footer class="footer">
    <div class="footer__brand">KERRO<small>CONSTRUCTION LTD</small></div>
    <span class="footer__item"><b>T:</b> +2348012345678</span>
    <span class="footer__item"><b>E:</b> hello@kerrobuild.com</span>
    <span class="footer__item"><b>W:</b> www.kerrobuild.com</span>
    <span class="footer__item"><b>A:</b> Palm Grove Road, Off Harbour Crescent, Sector 4, Lakeside City</span>
  </footer>
</section>

<!-- OCTOBER -->
<section class="page page--oct">
  <svg class="header-art" viewBox="0 0 385 312">
    <defs>
      <linearGradient id="band2" x1="0" y1="0" x2="1" y2="0"><stop offset="0" stop-color="#f2fde8"/><stop offset=".6" stop-color="#b5f57c"/><stop offset="1" stop-color="#8ef43a"/></linearGradient>
      <linearGradient id="photoOct" x1="0" y1="0" x2="0" y2="1"><stop offset="0" stop-color="#3f6b3a"/><stop offset=".5" stop-color="#6d5a3a"/><stop offset="1" stop-color="#a9502f"/></linearGradient>
    </defs>
    <path d="M0 0H385V48C300 36 220 60 150 85C90 104 40 98 0 86Z" fill="url(#band2)"/>
    <path d="M0 240C60 265 120 275 200 272C290 268 340 250 385 240V310C300 305 200 290 100 275C60 270 25 268 0 270Z" fill="url(#band2)"/>
    <path role="img" aria-label="Photo: aerial view of a red-earth road with an excavator beside a drainage channel" d="M0 84C60 96 110 82 190 56C260 34 330 35 385 40V222C330 242 250 260 180 256C100 252 40 252 0 260Z" fill="url(#photoOct)"/>
  </svg>
  <div class="brand"><span class="brand__mark"></span><div><div class="brand__name">KERRO</div><div class="brand__sub">CONSTRUCTION LTD</div></div></div>
  <div class="title-label">CALENDAR</div>
  <div class="title-year">2025</div>
  <div class="title-month" style="left:179px">OCTOBER</div>
  <div class="month-grid">
    <span class="wd">SUNDAY</span><span class="wd">MONDAY</span><span class="wd">TUESDAY</span><span class="wd">WEDNESDAY</span><span class="wd">THURSDAY</span><span class="wd">FRIDAY</span><span class="wd">SATURDAY</span>
    <span></span><span></span><span></span><span>1</span><span>2</span><span>3</span><span>4</span>
    <span>5</span><span>6</span><span>7</span><span>8</span><span>9</span><span>10</span><span>11</span>
    <span>12</span><span>13</span><span>14</span><span>15</span><span>16</span><span>17</span><span>18</span>
    <span>19</span><span>20</span><span>21</span><span>22</span><span>23</span><span>24</span><span>25</span>
    <span>26</span><span>27</span><span>28</span><span>29</span><span>30</span><span>31</span><span></span>
  </div>
  <div class="mini mini--a"><div class="mini__title">SEPTEMBER | <b>2025</b></div>
    <div class="mini__grid">
      <span class="wd">SUNDAY</span><span class="wd">MONDAY</span><span class="wd">TUESDAY</span><span class="wd">WEDNESDAY</span><span class="wd">THURSDAY</span><span class="wd">FRIDAY</span><span class="wd">SATURDAY</span>
      <span></span><span>1</span><span>2</span><span>3</span><span>4</span><span>5</span><span>6</span>
      <span>7</span><span>8</span><span>9</span><span>10</span><span>11</span><span>12</span><span>13</span>
      <span>14</span><span>15</span><span>16</span><span>17</span><span>18</span><span>19</span><span>20</span>
      <span>21</span><span>22</span><span>23</span><span>24</span><span>25</span><span>26</span><span>27</span>
      <span>28</span><span>29</span><span>30</span><span></span><span></span><span></span><span></span>
    </div></div>
  <div class="mini mini--b"><div class="mini__title">NOVEMBER | <b>2025</b></div>
    <div class="mini__grid">
      <span class="wd">SUNDAY</span><span class="wd">MONDAY</span><span class="wd">TUESDAY</span><span class="wd">WEDNESDAY</span><span class="wd">THURSDAY</span><span class="wd">FRIDAY</span><span class="wd">SATURDAY</span>
      <span>30</span><span></span><span></span><span></span><span></span><span></span><span>1</span>
      <span>2</span><span>3</span><span>4</span><span>5</span><span>6</span><span>7</span><span>8</span>
      <span>9</span><span>10</span><span>11</span><span>12</span><span>13</span><span>14</span><span>15</span>
      <span>16</span><span>17</span><span>18</span><span>19</span><span>20</span><span>21</span><span>22</span>
      <span>23</span><span>24</span><span>25</span><span>26</span><span>27</span><span>28</span><span>29</span>
    </div></div>
  <footer class="footer">
    <div class="footer__brand">KERRO<small>CONSTRUCTION LTD</small></div>
    <span class="footer__item"><b>T:</b> +2348012345678</span>
    <span class="footer__item"><b>E:</b> hello@kerrobuild.com</span>
    <span class="footer__item"><b>W:</b> www.kerrobuild.com</span>
    <span class="footer__item"><b>A:</b> Palm Grove Road, Off Harbour Crescent, Sector 4, Lakeside City</span>
  </footer>
</section>

<!-- NOVEMBER -->
<section class="page page--nov">
  <svg class="header-art" viewBox="0 0 385 312">
    <defs>
      <linearGradient id="band3" x1="0" y1="0" x2="1" y2="0"><stop offset="0" stop-color="#f2fde8"/><stop offset=".6" stop-color="#b5f57c"/><stop offset="1" stop-color="#8ef43a"/></linearGradient>
      <linearGradient id="photoNov" x1="0" y1="0" x2="0" y2="1"><stop offset="0" stop-color="#c9cccd"/><stop offset=".4" stop-color="#8f9496"/><stop offset="1" stop-color="#777c80"/></linearGradient>
    </defs>
    <path d="M0 0H385V48C300 36 220 60 150 85C90 104 40 98 0 86Z" fill="url(#band3)"/>
    <path d="M0 240C60 265 120 275 200 272C290 268 340 250 385 240V310C300 305 200 290 100 275C60 270 25 268 0 270Z" fill="url(#band3)"/>
    <path role="img" aria-label="Photo: finished interlocking-paver estate road with painted kerbs and lane markings" d="M0 84C60 96 110 82 190 56C260 34 330 35 385 40V222C330 242 250 260 180 256C100 252 40 252 0 260Z" fill="url(#photoNov)"/>
  </svg>
  <div class="brand"><span class="brand__mark"></span><div><div class="brand__name">KERRO</div><div class="brand__sub">CONSTRUCTION LTD</div></div></div>
  <div class="title-label">CALENDAR</div>
  <div class="title-year">2025</div>
  <div class="title-month" style="left:159px">NOVEMBER</div>
  <div class="month-grid">
    <span class="wd">SUNDAY</span><span class="wd">MONDAY</span><span class="wd">TUESDAY</span><span class="wd">WEDNESDAY</span><span class="wd">THURSDAY</span><span class="wd">FRIDAY</span><span class="wd">SATURDAY</span>
    <span>30</span><span></span><span></span><span></span><span></span><span></span><span>1</span>
    <span>2</span><span>3</span><span>4</span><span>5</span><span>6</span><span>7</span><span>8</span>
    <span>9</span><span>10</span><span>11</span><span>12</span><span>13</span><span>14</span><span>15</span>
    <span>16</span><span>17</span><span>18</span><span>19</span><span>20</span><span>21</span><span>22</span>
    <span>23</span><span>24</span><span>25</span><span>26</span><span>27</span><span>28</span><span>29</span>
  </div>
  <div class="mini mini--a"><div class="mini__title">OCTOBER | <b>2025</b></div>
    <div class="mini__grid">
      <span class="wd">SUNDAY</span><span class="wd">MONDAY</span><span class="wd">TUESDAY</span><span class="wd">WEDNESDAY</span><span class="wd">THURSDAY</span><span class="wd">FRIDAY</span><span class="wd">SATURDAY</span>
      <span></span><span></span><span></span><span>1</span><span>2</span><span>3</span><span>4</span>
      <span>5</span><span>6</span><span>7</span><span>8</span><span>9</span><span>10</span><span>11</span>
      <span>12</span><span>13</span><span>14</span><span>15</span><span>16</span><span>17</span><span>18</span>
      <span>19</span><span>20</span><span>21</span><span>22</span><span>23</span><span>24</span><span>25</span>
      <span>26</span><span>27</span><span>28</span><span>29</span><span>30</span><span>31</span><span></span>
    </div></div>
  <div class="mini mini--b"><div class="mini__title">DECEMBER | <b>2025</b></div>
    <div class="mini__grid">
      <span class="wd">SUNDAY</span><span class="wd">MONDAY</span><span class="wd">TUESDAY</span><span class="wd">WEDNESDAY</span><span class="wd">THURSDAY</span><span class="wd">FRIDAY</span><span class="wd">SATURDAY</span>
      <span></span><span>1</span><span>2</span><span>3</span><span>4</span><span>5</span><span>6</span>
      <span>7</span><span>8</span><span>9</span><span>10</span><span>11</span><span>12</span><span>13</span>
      <span>14</span><span>15</span><span>16</span><span>17</span><span>18</span><span>19</span><span>20</span>
      <span>21</span><span>22</span><span>23</span><span>24</span><span>25</span><span>26</span><span>27</span>
      <span>28</span><span>29</span><span>30</span><span>31</span><span></span><span></span><span></span>
    </div></div>
  <footer class="footer">
    <div class="footer__brand">KERRO<small>CONSTRUCTION LTD</small></div>
    <span class="footer__item"><b>T:</b> +2348012345678</span>
    <span class="footer__item"><b>E:</b> hello@kerrobuild.com</span>
    <span class="footer__item"><b>W:</b> www.kerrobuild.com</span>
    <span class="footer__item"><b>A:</b> Palm Grove Road, Off Harbour Crescent, Sector 4, Lakeside City</span>
  </footer>
</section>

</body>
</html>
```